KLV Plant Services

We are a heavy diesel mechanical business with additional air con certificates, remapping engine rebuilt

Contact Information for Business Card

Company Name, Director Name, Managing Director, Contact details, email and website

Font styles to use
Serif
Script

```html
<!DOCTYPE html>
<html lang="en">
<head>
<meta charset="utf-8">
<title>KLV Plant Services – Business Card</title>
<link href="https://fonts.googleapis.com/css2?family=Open+Sans:wght@400;600;700&display=swap" rel="stylesheet">
<style>
  :root {
    --backdrop: #3a3a3a;
    --backdrop-light: #5a5a5a;
    --card-white: #ffffff;
    --card-black: #000000;
    --brand-navy: #2b2a78;
    --text-light: #f2f2f2;
  }
  * { box-sizing: border-box; margin: 0; padding: 0; }
  html, body { width: 1200px; height: 780px; overflow: hidden; }
  body {
    background: radial-gradient(ellipse at 25% 10%, var(--backdrop-light), var(--backdrop) 70%);
    font-family: "Open Sans", Arial, sans-serif;
    position: relative;
  }
  .card {
    position: absolute;
    top: 235px;
    width: 540px;
    height: 310px;
    border-radius: 18px;
    overflow: hidden;
    background: var(--card-white);
    box-shadow: 0 14px 30px rgba(0,0,0,.45);
  }
  .card--back { left: 50px; }
  .card--front { left: 610px; }
  .card__shape { position: absolute; inset: 0; }

  .brand {
    position: absolute;
    display: flex;
    align-items: center;
    gap: 10px;
    color: var(--brand-navy);
    font-weight: 700;
    white-space: nowrap;
  }
  .brand__dot {
    border-radius: 50%;
    background: var(--brand-navy);
    flex: none;
  }
  .card--back .brand { left: 250px; top: 48px; font-size: 22px; }
  .card--back .brand__dot { width: 16px; height: 16px; }
  .card--front .brand { left: 50%; top: 50%; transform: translate(-50%, -50%); font-size: 38px; gap: 14px; }
  .card--front .brand__dot { width: 26px; height: 26px; }

  .person { position: absolute; left: 30px; top: 168px; }
  .person__name {
    color: var(--brand-navy);
    font-size: 17px;
    font-weight: 600;
    letter-spacing: .5px;
    text-transform: uppercase;
  }
  .person__role { color: var(--text-light); font-size: 12.5px; margin-top: 2px; }

  .divider {
    position: absolute;
    left: 218px; top: 186px;
    width: 1px; height: 62px;
    background: var(--brand-navy);
  }
  .contacts {
    position: absolute;
    left: 232px; top: 186px;
    list-style: none;
    color: var(--text-light);
    font-size: 13px;
    line-height: 21px;
  }
  .contacts li { display: flex; align-items: center; gap: 7px; }
  .contacts svg { width: 11px; height: 11px; fill: var(--text-light); flex: none; }
  .address {
    position: absolute;
    left: 30px; top: 262px;
    color: var(--text-light);
    font-size: 13px;
  }
</style>
</head>
<body>

<section class="card card--back" aria-label="Business card, contact side">
  <svg class="card__shape" viewBox="0 0 540 310" preserveAspectRatio="none" aria-hidden="true">
    <path d="M0,115 C200,110 380,200 540,150 L540,310 L0,310 Z" fill="var(--card-black)"/>
    <path d="M0,104 C200,99 380,189 540,139" fill="none" stroke="var(--brand-navy)" stroke-width="2.5"/>
  </svg>

  <div class="brand"><span class="brand__dot"></span>KLV Plant Services</div>

  <div class="person">
    <p class="person__name">Daniel Hart</p>
    <p class="person__role">Managing Director</p>
  </div>

  <span class="divider"></span>

  <ul class="contacts">
    <li>
      <svg viewBox="0 0 24 24"><path d="M6.6 10.8a15.1 15.1 0 0 0 6.6 6.6l2.2-2.2c.3-.3.7-.4 1-.2 1.1.4 2.3.6 3.6.6.6 0 1 .4 1 1V20c0 .6-.4 1-1 1A17 17 0 0 1 3 4c0-.6.4-1 1-1h3.5c.6 0 1 .4 1 1 0 1.3.2 2.5.6 3.6.1.3 0 .7-.2 1z"/></svg>
      123 456 789
    </li>
    <li>
      <svg viewBox="0 0 24 24"><path d="M2 5h20v14H2z M3.5 6.5 12 13l8.5-6.5" fill="none" stroke="var(--text-light)" stroke-width="2"/></svg>
      info@yourgmail.com
    </li>
    <li>
      <svg viewBox="0 0 24 24"><circle cx="12" cy="12" r="10" fill="none" stroke="var(--text-light)" stroke-width="2"/><path d="M2 12h20M12 2c3 3 3 17 0 20M12 2c-3 3-3 17 0 20" fill="none" stroke="var(--text-light)" stroke-width="1.6"/></svg>
      www.yourwebsite.com
    </li>
  </ul>

  <p class="address">Your address, City State, Zip 1234</p>
</section>

<section class="card card--front" aria-label="Business card, brand side">
  <div class="brand"><span class="brand__dot"></span>KLV Plant Services</div>
</section>

</body>
</html>
```